Business card for marketing analytics company

Need a business card for new company. I have a logo already that I want to be built into the card and should use those colours

Company is called steered by tallies
Design must bring steered by tallies to life not be a card that could be for anyone with a logo put on it.

Like the front to be fairly clean and uncluttered bringing the logo out with a suitable design on the back of the card.

The logo represents a compass and business growth so those themes along with numbers, analytics , data are appropriate.
I'm often working with creative industries so also needs to reflect the creative side of analytics rather than be very corporate looking.

Target Market(s)

Ad agency, media agency, consumer goods clients

Industry/Entity Type

Market Research

Contact Information for Business Card

Needs to include name, title, email and phone number

Colors
f78f20
f68d4d
ec1f27

Requirements
Must have
• Must bring steered by tallies to life not be a card that could be for anyone with a logo put on it.
• Logo, Correct colours
• Like a design on the back that relates to company name
• Designs for both sides
Should not have
• Please do not just submit logo and a coloured card.
• It needs to have a design element to it
• No black background
• No clear cards - needs front & back

```html
<!DOCTYPE html>
<html lang="en">
<head>
<meta charset="utf-8">
<title>Steered by Tallies – Business Card</title>
<link rel="stylesheet" href="https://fonts.googleapis.com/css2?family=Montserrat:wght@400;500;600;700&display=swap">
<style>
  :root {
    --canvas-bg: #c4c4c4;
    --card-light: #fbf6f0;
    --brand-orange: #f78f20;
    --brand-orange-deep: #f47321;
    --brand-peach: #f68d4d;
    --brand-red: #ec1f27;
    --tally-tint: rgba(247, 143, 32, 0.35);
    --text-white: #ffffff;
    --shadow: rgba(0, 0, 0, 0.25);
  }
  * { box-sizing: border-box; margin: 0; padding: 0; }
  html, body {
    width: 1200px;
    height: 1000px;
    overflow: hidden;
    background: var(--canvas-bg);
    font-family: "Montserrat", sans-serif;
  }
  .sheet {
    width: 1200px;
    height: 1000px;
    display: flex;
    align-items: center;
    justify-content: center;
    gap: 60px;
  }
  .card {
    position: relative;
    width: 540px;
    height: 310px;
    box-shadow: 0 2px 6px var(--shadow);
    overflow: hidden;
  }
  .card-back { background: var(--card-light); }
  .card-front {
    background: linear-gradient(135deg, var(--brand-orange) 0%, var(--brand-peach) 55%, var(--brand-orange-deep) 100%);
  }
  .card-shape {
    position: absolute;
    inset: 0;
    width: 100%;
    height: 100%;
  }
  .brand {
    position: absolute;
    display: flex;
    align-items: center;
    gap: 14px;
    font-weight: 500;
    line-height: 1.05;
  }
  .brand-dot {
    flex: none;
    border-radius: 50%;
    border: 3px solid currentColor;
  }
  .brand-name span { display: block; }
  .brand-back {
    left: 28px;
    top: 110px;
    color: var(--brand-orange-deep);
    font-size: 20px;
  }
  .brand-back .brand-dot { width: 54px; height: 54px; }
  .brand-front {
    left: 130px;
    top: 119px;
    color: var(--text-white);
    font-size: 27px;
  }
  .brand-front .brand-dot { width: 72px; height: 72px; }
  .tally-row {
    position: absolute;
    left: 28px;
    bottom: 34px;
    width: 200px;
    height: 40px;
  }
  .tally-front {
    left: auto;
    right: 28px;
    bottom: 24px;
    width: 120px;
    height: 28px;
  }
  .contact {
    position: absolute;
    right: 26px;
    top: 100px;
    text-align: right;
    color: var(--text-white);
  }
  .contact-name {
    font-size: 18px;
    font-weight: 700;
    letter-spacing: 0.5px;
  }
  .contact-title {
    font-size: 12px;
    font-weight: 500;
    letter-spacing: 0.5px;
    margin-top: 2px;
  }
  .contact-rule {
    width: 110px;
    height: 1px;
    background: var(--text-white);
    margin: 10px 0 14px auto;
  }
  .contact-list { list-style: none; }
  .contact-list li {
    display: flex;
    align-items: center;
    justify-content: flex-end;
    gap: 8px;
    font-size: 12px;
    margin-bottom: 6px;
  }
  .contact-icon {
    width: 16px;
    height: 16px;
    flex: none;
  }
</style>
</head>
<body>
<main class="sheet">

  <section class="card card-back" aria-label="Card back with contact details">
    <svg class="card-shape" viewBox="0 0 540 310" aria-hidden="true">
      <path fill="var(--brand-red)" d="M278 0 C222 90 236 240 318 310 L345 310 C262 232 246 84 295 0 Z"/>
      <path fill="var(--brand-orange-deep)" d="M295 0 C246 84 262 232 345 310 L540 310 L540 0 Z"/>
    </svg>

    <div class="brand brand-back">
      <span class="brand-dot"></span>
      <p class="brand-name"><span>Steered by</span><span>Tallies</span></p>
    </div>

    <svg class="tally-row" viewBox="0 0 200 40" aria-hidden="true">
      <g stroke="var(--tally-tint)" stroke-width="3" stroke-linecap="round">
        <path d="M6 6 V34 M16 6 V34 M26 6 V34 M36 6 V34 M0 30 L42 10"/>
        <path d="M62 6 V34 M72 6 V34 M82 6 V34 M92 6 V34 M56 30 L98 10"/>
        <path d="M118 6 V34 M128 6 V34 M138 6 V34"/>
      </g>
    </svg>

    <div class="contact">
      <p class="contact-name">DARA QUINN</p>
      <p class="contact-title">FOUNDER</p>
      <div class="contact-rule"></div>
      <ul class="contact-list">
        <li>000 000 0000
          <svg class="contact-icon" viewBox="0 0 16 16" aria-hidden="true">
            <circle cx="8" cy="8" r="7" fill="none" stroke="#fff" stroke-width="1.2"/>
            <path d="M5.5 4.5 L7 4.5 L7.5 6.5 L6.6 7.2 C7.1 8.3 7.8 9 8.9 9.5 L9.6 8.6 L11.5 9.1 L11.5 10.6 C8 10.8 5.3 8.1 5.5 4.5 Z" fill="#fff"/>
          </svg>
        </li>
        <li>info@daraquinn.com
          <svg class="contact-icon" viewBox="0 0 16 16" aria-hidden="true">
            <circle cx="8" cy="8" r="7" fill="none" stroke="#fff" stroke-width="1.2"/>
            <rect x="4.5" y="5.5" width="7" height="5" fill="none" stroke="#fff" stroke-width="1"/>
            <path d="M4.5 5.5 L8 8.3 L11.5 5.5" fill="none" stroke="#fff" stroke-width="1"/>
          </svg>
        </li>
        <li>tallieswebsite.com
          <svg class="contact-icon" viewBox="0 0 16 16" aria-hidden="true">
            <circle cx="8" cy="8" r="7" fill="none" stroke="#fff" stroke-width="1.2"/>
            <circle cx="8" cy="8" r="3.5" fill="none" stroke="#fff" stroke-width="1"/>
            <path d="M4.5 8 H11.5 M8 4.5 V11.5" stroke="#fff" stroke-width="0.8"/>
          </svg>
        </li>
      </ul>
    </div>
  </section>

  <section class="card card-front" aria-label="Card front with company name">
    <div class="brand brand-front">
      <span class="brand-dot"></span>
      <p class="brand-name"><span>Steered by</span><span>Tallies</span></p>
    </div>

    <svg class="tally-row tally-front" viewBox="0 0 120 28" aria-hidden="true">
      <g stroke="rgba(255,255,255,0.45)" stroke-width="2.5" stroke-linecap="round">
        <path d="M6 4 V24 M14 4 V24 M22 4 V24 M30 4 V24 M1 21 L35 7"/>
        <path d="M52 4 V24 M60 4 V24 M68 4 V24"/>
      </g>
    </svg>
  </section>

</main>
</body>
</html>
```